Social Media Graphics - Oakline Push REVISED

Create 6-7 individual social media graphics (square size) to encourage folks to join our online course called:

The Harvest Ledger Circle
How to Launch a Multi-Million Business From Scratch
Sign Up Today!

IMPORTANT: Make the largest and most prominent text on the graphic be: How to Launch a Multi-Million Business From Scratch

For the color scheme of the graphics, let's try a blue color palette; make sure the graphics appeal to both men and women

Make sure each graphic contains 1 of the 3 pics attached (crop pic as needed); and make sure one of the graphics is all TEXT only.

Target Market(s)

men and women looking to start a business

Industry/Entity Type

Entrepreneurship

Colors
0054AA
0677BA
7BADD7
CADEEF
E8F1F8

Requirements
Must have
• All the text and use the 3 pics provided; one graphic can be all text; Simple, modern design that's easy to read

```html
<!DOCTYPE html>
<html lang="en">
<head>
<meta charset="UTF-8">
<title>The Harvest Ledger Circle – Launch a Multi-Million Business</title>
<link rel="stylesheet" href="https://fonts.googleapis.com/css2?family=Poppins:wght@600;700&display=swap">
<style>
  :root {
    --brand-blue: #0054AA;
    --mid-blue: #0677BA;
    --soft-blue: #7BADD7;
    --pale-blue: #CADEEF;
    --ice-blue: #E8F1F8;
    --white: #ffffff;
    --shadow-navy: #0b2e63;
  }
  html, body {
    margin: 0;
    padding: 0;
    overflow: hidden;
    background: var(--brand-blue);
  }
  .canvas {
    position: relative;
    width: 1200px;
    height: 1200px;
    overflow: hidden;
    background: var(--brand-blue);
    font-family: "Poppins", sans-serif;
  }
  .backdrop {
    position: absolute;
    inset: 0;
  }
  .headline {
    position: absolute;
    left: 78px;
    top: 82px;
    margin: 0;
    color: var(--white);
    font-weight: 700;
    font-size: 116px;
    line-height: 106px;
    letter-spacing: 1px;
    text-transform: uppercase;
    text-shadow: 4px 4px 0 var(--shadow-navy);
  }
  .course-name {
    position: absolute;
    left: 78px;
    top: 622px;
    margin: 0;
    color: var(--white);
    font-weight: 600;
    font-size: 52px;
    line-height: 66px;
    letter-spacing: 1.5px;
    text-shadow: 3px 3px 0 var(--shadow-navy);
  }
  .cta-button {
    position: absolute;
    left: 72px;
    top: 886px;
    width: 341px;
    height: 79px;
    border-radius: 10px;
    background: var(--pale-blue);
    color: var(--brand-blue);
    font-weight: 700;
    font-size: 28px;
    display: flex;
    align-items: center;
    justify-content: center;
  }
  .hosts-photo {
    position: absolute;
    left: 445px;
    top: 535px;
    width: 755px;
    height: 665px;
    border-radius: 280px 280px 0 0;
    background: linear-gradient(160deg, #1c2a44 0%, #121826 45%, #1f4f86 100%);
  }
</style>
</head>
<body>
  <main class="canvas">
    <svg class="backdrop" width="1200" height="1200" viewBox="0 0 1200 1200" aria-hidden="true">
      <defs>
        <linearGradient id="orbFill" x1="0" y1="1" x2="1" y2="0">
          <stop offset="0" stop-color="#2a72b8"/>
          <stop offset="1" stop-color="#5e9fbd"/>
        </linearGradient>
      </defs>
      <circle cx="815" cy="-45" r="370" fill="url(#orbFill)"/>
      <path d="M0 1000 C 120 960, 230 990, 330 1000 C 450 1012, 560 980, 700 1000 L 700 1200 L 0 1200 Z" fill="#3a82c0"/>
    </svg>

    <h1 class="headline">How to Launch<br>a Multi-Million<br>Business From<br>Scratch</h1>

    <p class="course-name">The Harvest<br>Ledger Circle</p>

    <div class="cta-button">Sign Up Today!</div>

    <div class="hosts-photo" role="img" aria-label="Photo of the two course hosts standing side by side, smiling"></div>
  </main>
</body>
</html>
```